KRV Cartridge chip board folding ammuniton boxes for retail sale

Design a scalable design for use with 20 round and 50 round boxes for Ammunition. The caliber will be 9mm but will need to be editable, all warnings and barcodes will need to be able to be edited also. I have attached the company logo.

**UPDATE**
Box dimensions
20rd= 2.55in long X 2.1in width X 1.25in height

50rd= 5.1in long x 2.6in width X 1.2in height

Please see the bullet picture i would like used if possible.

Target Market(s)

Quality shooting sports, self defense

Industry/Entity Type

Self Defense

Requirements
Must have
• supplied company logo design
Should not have
• any cartoons of any kind

```html
<!DOCTYPE html>
<html lang="en">
<head>
<meta charset="utf-8">
<title>KRV Cartridge – 9mm 115gr 50 Round Box Layout</title>
<link href="https://fonts.googleapis.com/css2?family=Montserrat:ital,wght@0,700;0,800;0,900;1,800&display=swap" rel="stylesheet">
<style>
  :root {
    --page-bg: #f4f4f4;
    --red-bright: #b8191f;
    --red-mid: #8e1a1d;
    --red-deep: #5e1214;
    --badge-red: #6b1a1a;
    --steel-light: #c9cfcf;
    --steel-dark: #1f2d2d;
    --white: #ffffff;
    --ink: #0f1616;
    --brass-light: #f0dc98;
    --brass-dark: #9c7a24;
    --fold: rgba(0,0,0,.12);
  }
  * { margin: 0; padding: 0; box-sizing: border-box; }
  html, body { width: 1200px; height: 750px; overflow: hidden; background: var(--page-bg); }
  body { font-family: "Montserrat", sans-serif; position: relative; }

  .panel { position: absolute; overflow: hidden; outline: 1px solid var(--fold); }

  /* ---------- top panel ---------- */
  .panel-top {
    left: 268px; top: 52px; width: 867px; height: 204px;
    background: linear-gradient(100deg, var(--red-mid) 0%, var(--red-bright) 55%, #c4141a 100%);
    display: flex; align-items: center; justify-content: center; gap: 34px;
    color: var(--white);
  }
  .panel-top .brand-mark { font-size: 36px; }
  .panel-top .brand-dot { width: 30px; height: 30px; border-width: 4px; border-color: var(--white); }
  .panel-top .load-type { font-size: 18px; font-weight: 700; line-height: 1.35; }

  /* ---------- side panel ---------- */
  .panel-side { left: 64px; top: 256px; width: 204px; height: 442px; }
  .side-art { position: absolute; inset: 0; }
  .panel-side .brand-mark {
    position: absolute; left: 0; right: 0; top: 120px;
    justify-content: center; color: var(--white); font-size: 18px; gap: 8px;
  }
  .panel-side .brand-dot { width: 16px; height: 16px; border-width: 3px; border-color: var(--white); }
  .side-spec {
    position: absolute; left: 0; right: 0; top: 318px;
    text-align: center; color: var(--ink);
  }
  .side-spec .caliber { font-size: 26px; font-weight: 800; font-style: italic; line-height: 1.1; }
  .side-spec .load-type { font-size: 12px; font-weight: 700; line-height: 1.4; margin-top: 4px; }

  /* ---------- front panel ---------- */
  .panel-front { left: 268px; top: 256px; width: 867px; height: 442px; }
  .front-art { position: absolute; inset: 0; }

  .brand-mark {
    display: flex; align-items: center; gap: 14px;
    font-weight: 900; letter-spacing: 1px; white-space: nowrap;
  }
  .brand-dot { border-radius: 50%; border-style: solid; flex: none; }

  .panel-front .brand-mark {
    position: absolute; left: 230px; top: 62px;
    font-size: 48px; color: var(--ink);
  }
  .panel-front .brand-dot { width: 40px; height: 40px; border-width: 5px; border-color: var(--red-bright); }

  .count-badge {
    position: absolute; right: 18px; top: 0;
    width: 118px; height: 150px;
    background: var(--badge-red); color: var(--white);
    text-align: center; padding-top: 14px;
  }
  .count-badge .count { font-size: 68px; font-weight: 900; line-height: 1; }
  .count-badge .count-label { font-size: 19px; font-weight: 800; line-height: 1.05; margin-top: 5px; }

  .bullet-art {
    position: absolute; left: 62px; top: 170px;
    width: 110px; height: 255px;
    background: linear-gradient(90deg, var(--brass-dark), var(--brass-light) 45%, var(--brass-dark));
  }

  .headline {
    position: absolute; left: 228px; top: 300px;
    color: var(--white); font-weight: 900;
    font-size: 42px; line-height: 1.0; letter-spacing: 1px;
  }

  .front-spec { position: absolute; right: 30px; top: 215px; color: var(--white); }
  .front-spec .caliber { font-size: 42px; font-weight: 800; font-style: italic; line-height: 1.05; }
  .front-spec .load-type { font-size: 19px; font-weight: 700; line-height: 1.3; margin-top: 4px; }
</style>
</head>
<body>
  <section class="panel panel-top">
    <div class="brand-mark"><span class="brand-name">KRV Cartridge</span><span class="brand-dot"></span></div>
    <div class="load-type">FULL METAL JACKET<br>FMJ / ELITE AMMUNITION</div>
  </section>

  <section class="panel panel-side">
    <svg class="side-art" viewBox="0 0 204 442" width="204" height="442" aria-hidden="true">
      <defs>
        <linearGradient id="sideRed" x1="0" y1="0" x2="0" y2="1">
          <stop offset="0" stop-color="#6e1416"/>
          <stop offset="0.5" stop-color="#c0232a"/>
          <stop offset="1" stop-color="#8e1a1d"/>
        </linearGradient>
        <linearGradient id="sideSteel" x1="0" y1="0" x2="1" y2="0">
          <stop offset="0" stop-color="#c9cfcf"/>
          <stop offset="0.6" stop-color="#1f2d2d"/>
          <stop offset="1" stop-color="#c9cfcf"/>
        </linearGradient>
      </defs>
      <rect width="204" height="442" fill="url(#sideRed)"/>
      <rect y="268" width="204" height="24" fill="url(#sideSteel)"/>
      <rect y="292" width="204" height="150" fill="#eef0f0"/>
    </svg>
    <div class="brand-mark"><span class="brand-name">KRV Cartridge</span><span class="brand-dot"></span></div>
    <div class="side-spec">
      <div class="caliber">9mm 115gr</div>
      <div class="load-type">FULL METAL JACKET<br>FMJ / ELITE AMMUNITION</div>
    </div>
  </section>

  <section class="panel panel-front">
    <svg class="front-art" viewBox="0 0 867 442" width="867" height="442" aria-hidden="true">
      <defs>
        <linearGradient id="frontRed" x1="0" y1="0" x2="1" y2="1">
          <stop offset="0" stop-color="#8e1a1d"/>
          <stop offset="0.6" stop-color="#7d1518"/>
          <stop offset="1" stop-color="#5e1214"/>
        </linearGradient>
        <linearGradient id="frontSteel" x1="0" y1="0" x2="1" y2="0">
          <stop offset="0" stop-color="#c9cfcf"/>
          <stop offset="0.5" stop-color="#1f2d2d"/>
          <stop offset="0.8" stop-color="#2f3d3d"/>
          <stop offset="1" stop-color="#c9cfcf"/>
        </linearGradient>
      </defs>
      <rect width="867" height="442" fill="url(#frontRed)"/>
      <path d="M0 0 H867 V155 Q700 200 500 240 Q250 290 0 325 Z" fill="url(#frontSteel)"/>
      <path d="M0 0 H867 V130 Q700 175 500 215 Q250 265 0 300 Z" fill="#ffffff"/>
    </svg>

    <div class="brand-mark"><span class="brand-name">KRV Cartridge</span><span class="brand-dot"></span></div>

    <div class="count-badge">
      <div class="count">50</div>
      <div class="count-label">Cartridge<br>per box</div>
    </div>

    <div class="bullet-art" role="img" aria-label="Photograph of a brass 9mm full metal jacket cartridge"></div>

    <h1 class="headline">ELITE<br>PERFORMANCE<br>AMMUNITION</h1>

    <div class="front-spec">
      <div class="caliber">9mm 115gr</div>
      <div class="load-type">FULL METAL JACKET<br>FMJ / ELITE AMMUNITION</div>
    </div>
  </section>
</body>
</html>
```